3D Animation for Screen on Entry Gate

We need 2 x 3D Animations for the entry screen that will sit on top of a turnstile as you enter a venue. These images need to be very clear, modern looking animated images.

1) The first animation will need to be a moving flashing or moving from small to large, Red Cross that also reads "Invalid"
2) The 2nd image needs to have the same look and feel but be a moving Green arrow - moving from the bottom of the screen to the top of the screen that also reads Access Granted

We will require the file to be provided as a mp4. thank you.

```html
<!DOCTYPE html>
<html lang="en">
<head>
<meta charset="UTF-8">
<title>Invalid Entry Screen</title>
<link href="https://fonts.googleapis.com/css2?family=Rajdhani:wght@600&display=swap" rel="stylesheet">
<style>
  :root {
    --bg: #000000;
    --glow: #1a0403;
    --alert-red: #ff1a1a;
    --panel-red: rgba(120, 10, 10, 0.55);
    --panel-edge: rgba(255, 40, 40, 0.35);
    --cross-face: rgba(190, 30, 30, 0.82);
    --cross-side: rgba(110, 15, 15, 0.9);
    --ring-orange: #e07a2a;
    --ring-amber: #f0a040;
  }
  html, body {
    margin: 0;
    padding: 0;
    width: 1200px;
    height: 676px;
    overflow: hidden;
    background: var(--bg);
  }
  .screen {
    position: relative;
    width: 1200px;
    height: 676px;
    overflow: hidden;
    background: var(--bg);
  }
  .backdrop {
    position: absolute;
    inset: 0;
    background: radial-gradient(ellipse at 50% 45%, var(--glow) 0%, var(--bg) 60%);
  }
  .stage,
  .cross,
  .accents {
    position: absolute;
    inset: 0;
  }
  .status-label {
    position: absolute;
    left: 336px;
    top: 276px;
    width: 534px;
    margin: 0;
    text-align: center;
    font-family: "Rajdhani", sans-serif;
    font-weight: 600;
    font-size: 84px;
    line-height: 100px;
    letter-spacing: 0.3em;
    text-indent: 0.3em;
    color: var(--alert-red);
    white-space: nowrap;
  }
</style>
</head>
<body>
  <main class="screen">
    <div class="backdrop" role="img" aria-label="Dark space backdrop with faint orange particle network"></div>

    <svg class="stage" width="1200" height="676" viewBox="0 0 1200 676" aria-hidden="true">
      <g class="base-rings" fill="none">
        <ellipse cx="600" cy="504" rx="362" ry="52" stroke="var(--ring-orange)" stroke-width="1.5" stroke-dasharray="2 3" opacity="0.7"/>
        <ellipse cx="600" cy="504" rx="340" ry="44" stroke="var(--ring-orange)" stroke-width="2.5" opacity="0.8"/>
        <ellipse cx="600" cy="500" rx="292" ry="34" stroke="var(--ring-amber)" stroke-width="3"/>
        <ellipse cx="600" cy="498" rx="250" ry="26" stroke="var(--ring-orange)" stroke-width="1.5" opacity="0.6"/>
      </g>

      <g class="status-panel">
        <rect x="336" y="242" width="534" height="172" rx="8" fill="var(--panel-red)" stroke="var(--panel-edge)" stroke-width="2"/>
        <path d="M332 330 V230 H408" fill="none" stroke="var(--alert-red)" stroke-width="5" stroke-linecap="round"/>
        <path d="M546 230 H872 Q882 230 882 240 V330" fill="none" stroke="var(--alert-red)" stroke-width="5" stroke-linecap="round"/>
        <path d="M326 340 V420 Q326 426 334 426 H872 Q882 426 882 416 V380" fill="none" stroke="var(--panel-edge)" stroke-width="2"/>
      </g>
    </svg>

    <svg class="cross" width="1200" height="676" viewBox="0 0 1200 676" aria-hidden="true">
      <g class="cross-mark">
        <polygon points="492,192 470,206 732,484 754,470" fill="var(--cross-side)"/>
        <polygon points="708,192 730,206 470,484 448,470" fill="var(--cross-side)"/>
        <polygon points="492,192 434,244 696,480 754,428" fill="var(--cross-face)"/>
        <polygon points="708,192 766,244 504,480 446,428" fill="var(--cross-face)"/>
      </g>
    </svg>

    <svg class="accents" width="1200" height="676" viewBox="0 0 1200 676" aria-hidden="true">
      <path class="dash-accent" d="M378 436 H402 M410 436 H420 M428 436 H434" stroke="var(--alert-red)" stroke-width="5"/>
    </svg>

    <p class="status-label">INVALID</p>
  </main>
</body>
</html>
```